Card Design for my dog training business Brightpaw Obedience

Need a business card design for my dog training business with my new logo. Want the card to come off professional yet fun. Want it to be very eye catchy as well. I normally have these at vet clinics, pet stores, and groomers. so need it to look better than my competitors.
Target Market(s)
dog owners
Industry/Entity Type
Dog Training
Contact Information for Business Card
needs logo, my name and info
Font styles to use
Serif
Colors
0255a3
ffffff
ec1f27
000000
333333
fbfbfb
Requirements
Must have
- Brightpaw Obedience
- Felix Orland
- 415 903 2276
- info@brightpawobedience.example
- www.brightpawobedience.example

```html
<!DOCTYPE html>
<html lang="en">
<head>
<meta charset="utf-8">
<title>Brightpaw Obedience – Business Card</title>
<link rel="stylesheet" href="https://fonts.googleapis.com/css2?family=EB+Garamond:ital@1&family=Noto+Serif:wght@400&family=Open+Sans:wght@400&display=swap">
<style>
  :root {
    --blue: #0255a3;
    --red: #ec1f27;
    --charcoal: #333333;
    --black: #000000;
    --white: #ffffff;
    --card: #fbfbfb;
    --backdrop: #c9c9c9;
  }
  * { margin: 0; padding: 0; box-sizing: border-box; }
  html, body {
    width: 1200px; height: 576px; overflow: hidden;
    background: var(--backdrop);
  }
  .stage { position: relative; width: 1200px; height: 576px; }
  .card {
    position: absolute; top: 138px;
    width: 485px; height: 294px;
    background: var(--card);
    border-radius: 12px;
    overflow: hidden;
  }
  .card--back { left: 82px; }
  .card--front { left: 602px; }

  .brand {
    position: absolute;
    display: flex; flex-direction: column; align-items: center; gap: 10px;
    font-family: "Noto Serif", serif; font-weight: 400;
    color: var(--charcoal);
    text-align: center; line-height: 1.15;
  }
  .brand__dot {
    width: 34px; height: 34px; border-radius: 50%;
    background: var(--charcoal);
  }
  .card--back .brand { left: 0; right: 0; top: 72px; font-size: 26px; }
  .card--front .brand { left: 20px; width: 190px; top: 122px; font-size: 21px; }

  .tagline {
    font-family: "EB Garamond", serif; font-style: italic;
  }
  .back-band {
    position: absolute; left: 0; right: 0; top: 255px; height: 28px;
    background: var(--blue);
    display: flex; align-items: center; justify-content: center;
  }
  .back-band .tagline { color: var(--white); font-size: 12.5px; }

  .swoosh { position: absolute; left: 0; top: 0; }
  .identity {
    position: absolute; right: 33px; top: 24px; text-align: right;
    font-family: "Noto Serif", serif; color: var(--white);
  }
  .identity__name { font-size: 20px; font-weight: 400; line-height: 1.2; }
  .identity__role { font-size: 12px; margin-top: 3px; }

  .contacts {
    position: absolute; right: 33px; top: 181px;
    list-style: none;
    font-family: "Open Sans", sans-serif; font-size: 12.5px;
    color: var(--charcoal);
  }
  .contacts li {
    display: flex; align-items: center; justify-content: flex-end;
    gap: 10px; height: 19px;
  }
  .contacts svg { width: 11px; height: 11px; fill: var(--blue); flex: none; }
  .card--front .tagline {
    position: absolute; right: 40px; top: 248px;
    font-size: 12.5px; color: var(--charcoal);
  }
</style>
</head>
<body>
<main class="stage">

  <section class="card card--back" aria-label="Business card back">
    <div class="brand">
      <span class="brand__dot"></span>
      <span class="brand__name">Brightpaw<br>Obedience</span>
    </div>
    <div class="back-band">
      <p class="tagline">“Bright habits for happy dogs, one paw at a time.”</p>
    </div>
  </section>

  <section class="card card--front" aria-label="Business card front">
    <svg class="swoosh" width="485" height="294" viewBox="0 0 485 294" aria-hidden="true">
      <path fill="var(--charcoal)" d="M0 0H485V102C420 110 350 72 260 42C180 20 70 28 0 58Z"/>
      <path fill="var(--red)" d="M0 58C70 28 180 20 245 36C180 30 80 44 0 76Z"/>
      <path fill="var(--blue)" d="M0 82C80 46 190 32 262 44C350 66 410 110 485 106V124C410 126 345 86 262 54C185 40 80 56 0 88Z"/>
    </svg>

    <header class="identity">
      <h1 class="identity__name">Felix Orland</h1>
      <p class="identity__role">Dog Trainer</p>
    </header>

    <div class="brand">
      <span class="brand__dot"></span>
      <span class="brand__name">Brightpaw<br>Obedience</span>
    </div>

    <ul class="contacts">
      <li>415 903 2276
        <svg viewBox="0 0 12 12"><path d="M1 4C1 2 3 1 6 1S11 2 11 4V5H8.5V3.8H3.5V5H1Z"/><path d="M2.5 6H9.5L10.5 11H1.5Z"/></svg>
      </li>
      <li>info@brightpawobedience.example
        <svg viewBox="0 0 12 12"><path d="M0 2.5H12V10H0Z"/><path d="M0.5 3L6 7L11.5 3" fill="none" stroke="var(--card)" stroke-width="1"/></svg>
      </li>
      <li>www.brightpawobedience.example
        <svg viewBox="0 0 12 12"><circle cx="6" cy="6" r="5.5"/><path d="M0.5 6H11.5M6 0.5V11.5M6 0.5C3 3.5 3 8.5 6 11.5M6 0.5C9 3.5 9 8.5 6 11.5" fill="none" stroke="var(--card)" stroke-width="0.8"/></svg>
      </li>
    </ul>

    <p class="tagline">“Bright habits for happy dogs, one paw at a time.”</p>
  </section>

</main>
</body>
</html>
```